New Branding Concept Healthcare Course Brochure

OBJECTIVE:
We need a new course brochure design to meet match our new branding colour scheme & concept as we are currently in the process of upgrading our website design. This A4 double sided brochure will briefly showcase a course on offer, in a clear, concise, professional and engaging way. This brochure will be in line with our new branding colour scheme and concept.
Our concept in monochrome with spashes & pops of colour (matching our logo colours) - see examples attached of imagery being used for social media currently as this somewhat reflects the concept we are working towards after, in terms of colour and look.

We are happy for you to be creative with formats. However, it must be able to include the same information as attached in "disability course brochure information". Have also attached some 'format examples' that we like - this is purely for ideas of paragraphing and formatting of information that other training providers are using, not for colour and graphic examples.

The final design will be used for promotional and adverting purposes to communicate information about a course to a prospective student in both print and soft copy form.

ORGANISATION OVERVIEW:
Brightward Learning (RTO.47318)
03 9417 2856
www.brightwardlearning.edu.au
admin@bwl.edu.au
Head Office (Admin only): Level 4, 57 Corlette Street, Blackburn VIC 3130
3 modern & fully equipped training campuses across Melbourne: Blackburn (Tallowood Road), Preston & Narre Warren.
We are a private registered training organisation based in Melbourne, Victoria, Australia specialising in only healthcare courses such as certificate III in pathology collection, Certificate IV in Disability, Certificate III in individual Support, Certificate IV in Aged Care & Certificate III in Health Services Assistance. We also offer professional development training workshops to corporate clients and the public such as first aid, cpr, medications, food saftey, manual handling and much more.

Target Market(s)

Prospective Healthcare Education Students

Font styles to use
Serif

Colors
f37122
fbed22
ffffff

Requirements
Must have
• MUST INCLUDE:
- QVS Logo (attached)
- Our Logo (attached)
- Our slogan (Making you the future of healthcare)
- QR Code
- pops of colour must match our logo colours (see guide attached)
- contact details: website, social media buttons (instagram, facebook & twitter), phone number, email & our head office address.
- Must include relevant imagery (in this case disability or disability carer related, steer away from wheelchair images as it's used too much)
- must include information items (as per attached "disability brochure course information"

```html
<!DOCTYPE html>
<html lang="en">
<head>
<meta charset="utf-8">
<title>Brightward Learning – Certificate IV in Disability Brochure</title>
<link rel="stylesheet" href="https://fonts.googleapis.com/css2?family=Oswald:wght@400;500&family=Source+Sans+3:wght@400;600;700&family=Montserrat:wght@700;800&display=swap">
<style>
:root{
  --orange:#f37122;
  --orange-deep:#ef5a24;
  --yellow:#fbed22;
  --white:#ffffff;
  --ink:#3a3a3a;
  --grey:#58595b;
  --sidebar:#e4e4e4;
  --footer:#4d4d4f;
  --stage:#e8e8e8;
}
*{box-sizing:border-box;margin:0;padding:0}
html,body{width:1200px;height:829px;overflow:hidden}
body{background:var(--stage);font-family:"Source Sans 3",Arial,sans-serif;color:var(--ink);position:relative}
.page{position:absolute;top:78px;width:486px;height:688px;background:var(--white);overflow:hidden;box-shadow:0 2px 8px rgba(0,0,0,.25)}
.page--front{left:106px}
.page--back{left:630px}
.abs{position:absolute}
/* header */
.brand{position:absolute;left:18px;top:22px;display:flex;align-items:center;gap:7px}
.brand__dot{width:22px;height:22px;border-radius:50%;background:var(--orange)}
.brand__name{font-family:"Source Sans 3",sans-serif;font-weight:600;font-size:17px;line-height:17px;color:var(--grey);width:110px}
.brand__rto{position:absolute;left:47px;top:40px;font-size:4.5px;color:var(--grey);letter-spacing:.3px}
.slogan{position:absolute;right:16px;top:36px;font-family:"Oswald",sans-serif;font-size:12.5px;color:var(--ink);letter-spacing:-.1px}
.header-rule{position:absolute;left:220px;right:0;top:69px;height:9px;background:var(--orange);clip-path:polygon(14px 0,100% 0,100% 100%,0 100%)}
/* photo placeholders */
.photo{position:absolute;background:linear-gradient(120deg,#9a9a9a,#d8d8d8 55%,#8a8a8a)}
/* overview */
.overview{position:absolute;left:0;top:80px;width:390px;height:184px;background:var(--orange-deep);clip-path:polygon(0 0,215px 0,335px 184px,0 184px);color:var(--white);padding:20px 15px}
.overview h2{font-size:13px;font-weight:600;margin-bottom:4px}
.overview__bar{width:78px;height:2px;background:var(--yellow);margin-bottom:10px}
.overview p{font-size:6.6px;line-height:8px;width:245px;margin-bottom:8px}
/* body text */
h3{color:var(--orange);font-size:9px;font-weight:700;margin-bottom:2px}
.body p{font-size:6.4px;line-height:7.6px;margin-bottom:5px}
.body b{font-weight:700}
.col-left{position:absolute;left:15px;top:278px;width:283px}
.col-left section{margin-bottom:10px}
.sidebar{position:absolute;left:311px;top:264px;width:175px;height:396px;background:var(--sidebar);padding:14px 10px}
.sidebar h4{font-family:"Oswald",sans-serif;font-weight:500;font-size:12.5px;color:var(--ink);margin-left:26px;margin-bottom:14px}
.badge{position:absolute;right:8px;top:12px;width:30px;height:18px;background:#3a9a5b}
.prospect{display:flex;gap:7px;margin-bottom:10px}
.prospect__icon{flex:none;width:20px;height:20px;border-radius:50%;background:var(--orange);display:flex;align-items:center;justify-content:center}
.prospect h5{color:var(--orange);font-size:7.6px;font-weight:600;margin-bottom:1px}
.prospect p,.prospect li{font-size:6.4px;line-height:7.6px}
.prospect ul{list-style:none}
.prospect li::before{content:"";display:inline-block;width:4px;height:4px;border-radius:50%;background:var(--orange);margin-right:4px;vertical-align:1px}
.notice{background:var(--orange-deep);color:var(--white);font-size:6px;line-height:7.4px;text-align:center;padding:10px 8px;border-radius:0 0 8px 8px;margin:14px 0 22px}
.questions h6{font-size:10px;font-weight:400;margin-bottom:3px}
.questions p{font-size:6.2px;line-height:7.4px;margin-bottom:5px}
.contact{display:flex;gap:5px;font-size:6.2px;line-height:7px;margin-bottom:3px;align-items:flex-start}
.contact span.dot{flex:none;width:7px;height:7px;border-radius:50%;background:var(--orange)}
/* footer */
.footer{position:absolute;left:0;right:0;bottom:0;height:29px;background:var(--footer);color:var(--white);font-size:8.5px;display:flex;align-items:center;padding-left:16px;gap:16px}
.footer__item{display:flex;align-items:center;gap:5px}
.footer__icon{width:9px;height:9px;border-radius:50%;background:var(--orange)}
.footer__cta{position:absolute;right:0;bottom:0;height:42px;width:200px;background:var(--orange-deep);clip-path:polygon(26px 0,100% 0,100% 100%,0 100%);display:flex;align-items:flex-end;justify-content:flex-end;padding:0 10px 8px 0;font-family:"Oswald",sans-serif;font-size:14px;gap:4px;color:var(--white)}
.page--back .footer__cta{width:210px}
.socials{position:absolute;right:12px;bottom:44px;display:flex;gap:3px}
.socials i{width:8px;height:8px;border-radius:50%;border:1px solid #c9c9c9;display:block}
/* back hero */
.hero-text{position:absolute;left:112px;top:140px;color:var(--white);font-family:"Montserrat",sans-serif;font-weight:800;font-size:29px;line-height:23px;letter-spacing:-.5px;text-shadow:0 1px 3px rgba(0,0,0,.3)}
.hero-cta{position:absolute;left:112px;top:216px;color:var(--yellow);font-family:"Montserrat",sans-serif;font-weight:700;font-size:14px}
.hero-strip{position:absolute;left:0;right:0;top:278px;height:14px;background:var(--orange-deep)}
.growth{position:absolute;left:377px;top:222px;width:92px;height:92px;border-radius:50%;background:var(--orange);border:4px solid var(--yellow);color:var(--white);font-family:"Montserrat",sans-serif;font-weight:800;font-size:12px;line-height:11px;padding:24px 0 0 14px}
/* units table */
.units{position:absolute;left:15px;top:296px;width:458px}
.units p{font-size:6.5px;line-height:8px;margin-bottom:10px}
.tables{display:flex;gap:3px}
table{border-collapse:collapse;font-size:4.6px;background:#ececec}
th{background:var(--yellow);color:var(--ink);font-size:5.6px;font-weight:600;height:12px;text-align:center}
th.key{background:var(--orange-deep);color:var(--white)}
td{height:11.2px;padding:0 5px;border-bottom:1px solid #f8f8f8}
td.code{width:50px;border-right:1px solid #fff}
.t-core{width:230px}
.t-elective{width:225px}
.units small{display:block;text-align:center;font-size:4.6px;font-style:italic;margin-top:5px}
.col-a{position:absolute;left:15px;top:516px;width:225px}
.col-b{position:absolute;left:249px;top:516px;width:225px}
.col-a section,.col-b section{margin-bottom:8px}
.apply{position:absolute;left:15px;top:630px;width:230px;font-size:6.4px;line-height:7.6px}
.apply span{color:var(--orange)}
</style>
</head>
<body>

<!-- FRONT -->
<article class="page page--front">
  <header>
    <div class="brand"><span class="brand__dot"></span><span class="brand__name">Brightward Learning</span></div>
    <span class="brand__rto">RTO.47318</span>
    <p class="slogan">MAKING YOU THE FUTURE OF HEALTHCARE</p>
    <div class="header-rule"></div>
  </header>

  <div class="photo" style="left:200px;top:80px;width:286px;height:184px" role="img" aria-label="Monochrome photo of a carer smiling with an elderly woman holding a walking cane"></div>
  <section class="overview">
    <h2>Course Overview</h2>
    <div class="overview__bar"></div>
    <p>Start your rewarding career in disability with Brightward Learning and become a job-ready disability support worker (DSW).</p>
    <p>This qualification reflects the role of workers in a range of community settings and clients' homes, who provide training and support in a manner that empowers people with disabilities to achieve greater levels of independence, self-reliance, community participation and wellbeing, workers promote a person-centred approach and more.</p>
    <p>Brightward Learning is committed to providing an inclusive learning environment. Principles of access and equity for all students are applied in all programs. People with disabilities are encouraged to apply.</p>
  </section>

  <div class="col-left body">
    <section>
      <h3>Practical experience and assessment:</h3>
      <p>Is undertaken throughout the course in the Brightward Learning simulated environment with trainers who are experts in their field and maintain currency in the industry.</p>
    </section>
    <section>
      <h3>Course Entry Requirements</h3>
      <p>This is an open entry program of study with participants needing to read, write and communicate in English to a level to perform the job.<br>For further detailed information regarding entry requirements, please visit: <b>www.brightwardlearning.edu.au/certificate-4-in-disability</b></p>
    </section>
    <section>
      <h3>Govt. Subsidised Training</h3>
      <p>This training is delivered with Victorian and Commonwealth Government funding under the Skills First Program and may impact your access to further government subsidised training.</p>
      <p>To find out if you are eligible, please contact us on 03 9417 2856 to discuss your circumstances or visit: <b>https://www.brightwardlearning.edu.au/funded-courses.html</b></p>
    </section>
    <section>
      <h3>Tuition Fees</h3>
      <p>The student tuition fees as published are subject to change given individual circumstances at enrolment.</p>
      <p>Full Fee: <b>$3,200</b><br>Government Funded: <b>$250</b><br>Government Funded With Health Care Card, Pensioner Concession Card or Vet Gold Card: <b>$250</b></p>
      <p>For detailed information regarding our course fees &amp; payment plans available please visit: <b>www.brightwardlearning.edu.au/certificate-4-in-disability</b></p>
    </section>
    <section>
      <h3>Practical Placement</h3>
      <p>Practical placement of 120 hours is a mandatory requirement of this course. Brightward Learning will organise on our students behalf.</p>
    </section>
  </div>

  <aside class="sidebar">
    <span class="badge" role="img" aria-label="QVS recognition badge"></span>
    <h4>JOB PROSPECTS</h4>
    <div class="prospect">
      <span class="prospect__icon"><svg width="10" height="10" viewBox="0 0 10 10"><circle cx="5" cy="3" r="2" fill="#fff"/><path d="M1 10a4 4 0 0 1 8 0z" fill="#fff"/></svg></span>
      <div><h5>Possible outcomes may include:</h5>
        <ul><li>Community Worker</li><li>Disabilities Services Officer</li><li>Disability Support Worker</li></ul></div>
    </div>
    <div class="prospect">
      <span class="prospect__icon"><svg width="10" height="10" viewBox="0 0 10 10"><path d="M5 0a3.5 3.5 0 0 1 3.5 3.5C8.5 6 5 10 5 10S1.5 6 1.5 3.5A3.5 3.5 0 0 1 5 0z" fill="#fff"/><circle cx="5" cy="3.5" r="1.3" fill="#f37122"/></svg></span>
      <div><h5>Delivery Locations:</h5><p>Blackburn, Narre Warren &amp; Preston</p></div>
    </div>
    <div class="prospect">
      <span class="prospect__icon"><svg width="10" height="10" viewBox="0 0 10 10"><rect x="1" y="2" width="8" height="7" fill="none" stroke="#fff"/><path d="M1 4h8M3 1v2M7 1v2" stroke="#fff"/></svg></span>
      <div><h5>Duration:</h5><p>• 22 weeks* of 1 day per week (9am-4.30pm) or;<br>• 30 weeks* of 1 evening per week (5pm-9pm) + 3 Saturdays (9am-4.30pm)</p></div>
    </div>
    <div class="prospect">
      <span class="prospect__icon"><svg width="10" height="10" viewBox="0 0 10 10"><rect x="1" y="2" width="8" height="5" fill="none" stroke="#fff"/><path d="M3 9h4" stroke="#fff"/></svg></span>
      <div><h5>Delivery Mode:</h5><p>Classroom &amp; blended/virtual learning</p></div>
    </div>
    <p class="notice">Delivery location &amp; duration varies between intakes. Please refer to our website at <b>www.brightwardlearning.edu.au</b> for upcoming course availability</p>
    <div class="questions">
      <h6>Questions?</h6>
      <p>Should you have any questions regarding Brightward Learning and the course, please contact one of our friendly team members on:</p>
      <div class="contact"><span class="dot"></span>03 9417 2856</div>
      <div class="contact"><span class="dot"></span>admin@bwl.edu.au</div>
      <div class="contact"><span class="dot"></span>Level 4, 57 Corlette Street, Blackburn VIC 3130<br>(Head Office)</div>
    </div>
  </aside>

  <div class="socials"><i></i><i></i><i></i></div>
  <footer class="footer">
    <span class="footer__item"><span class="footer__icon"></span>admin@bwl.edu.au</span>
    <span class="footer__item"><span class="footer__icon"></span>www.brightwardlearning.edu.au</span>
  </footer>
  <div class="footer__cta">
    <svg width="12" height="14" viewBox="0 0 12 14"><path d="M3 1h3l1 3-2 1a7 7 0 0 0 3 4l1-2 3 1v3c0 1-1 2-2 2C5 13 0 8 0 3c0-1 1-2 2-2z" fill="#fff"/></svg>
    03 9417 2856
  </div>
</article>

<!-- BACK -->
<article class="page page--back">
  <header>
    <div class="brand"><span class="brand__dot"></span><span class="brand__name">Brightward Learning</span></div>
    <span class="brand__rto">RTO.47318</span>
    <p class="slogan">MAKING YOU THE FUTURE OF HEALTHCARE</p>
    <div class="header-rule"></div>
  </header>

  <div class="photo" style="left:0;top:80px;width:486px;height:198px;background:linear-gradient(90deg,#6f6f6f,#a4a4a4 55%,#d2d2d2)" role="img" aria-label="Monochrome photo of a smiling male healthcare worker wearing glasses"></div>
  <h1 class="hero-text">making you<br>the future of<br>healthcare</h1>
  <p class="hero-cta">apply today!</p>
  <div class="hero-strip"></div>
  <div class="growth">higher<br>than<br>average<br>growth</div>

  <section class="units">
    <h3>Units of Competency</h3>
    <p>16 units of competency are required to successfully complete this qualification. This includes 11 core units and 5 elective units, along with 120 hours of practical work placement.</p>
    <div class="tables">
      <table class="t-core">
        <tr><th class="key">Core Units</th><th>Units of Competency</th></tr>
        <tr><td class="code">CHCCCS015</td><td>Provide individualised Support</td></tr>
        <tr><td class="code">CHCDIS002</td><td>Follow established person centred behaviour supports</td></tr>
        <tr><td class="code">CHCDIS005</td><td>Develop and provide person centred service responses</td></tr>
        <tr><td class="code">CHCDIS007</td><td>Facilitate the empowerment of people with disability</td></tr>
        <tr><td class="code">CHCDIS008</td><td>Facilitate community participation and social inclusion</td></tr>
        <tr><td class="code">CHCDIS009</td><td>Facilitate ongoing skills development using a person centred approach</td></tr>
        <tr><td class="code">CHCDIS010</td><td>Provide person centred services to people with disability with complex needs</td></tr>
        <tr><td class="code">CHCDIV001</td><td>Work with diverse people</td></tr>
        <tr><td class="code">CHCLEG003</td><td>Manage legal and ethical compliance</td></tr>
        <tr><td class="code">HLTAAP001</td><td>Recognise healthy body systems</td></tr>
        <tr><td class="code">HLTWHS002</td><td>Follow safe work practices for direct client care</td></tr>
      </table>
      <table class="t-elective">
        <tr><th class="key">Elective units</th><th>Units of Competency</th></tr>
        <tr><td class="code">HLTFSE001</td><td>Follow basic food safety practices</td></tr>
        <tr><td class="code">CHCCCS011</td><td>Meet personal support needs</td></tr>
        <tr><td class="code">CHCLAH001</td><td>Work effectively within the leisure and health industries</td></tr>
        <tr><td class="code">HLTAID003</td><td>Provide first aid</td></tr>
        <tr><td class="code">HLTINF001</td><td>Comply with infection prevention and control policies and procedures</td></tr>
        <tr><td class="code"></td><td></td></tr><tr><td class="code"></td><td></td></tr><tr><td class="code"></td><td></td></tr>
        <tr><td class="code"></td><td></td></tr><tr><td class="code"></td><td></td></tr><tr><td class="code"></td><td></td></tr>
      </table>
    </div>
    <small>Competency is assessed through a combination of practical application and demonstration of skills, research, analysis and completion of competency based workbooks.</small>
  </section>

  <div class="col-a body">
    <section>
      <h3>Opportunity for Credit Transfers (CT)</h3>
      <p>If students have already successfully completed unit/s of competency which are included within the qualification BWL offers, credit may be granted.</p>
    </section>
    <section>
      <h3>Opportunity for Recognition of Prior Learning (RPL)</h3>
      <p>Competencies gained through other formal study or experience may be acknowledged through a recognition process.</p>
    </section>
  </div>
  <div class="col-b body">
    <section>
      <h3>Pathways</h3>
      <p>A possible training pathway for a participant completing this qualification could be any specialised area in the health sector or courses similar to the following: Certificate IV in Community Services; Certificate IV in Leisure and Health; Certificate IV in Ageing Support; Diploma of Community Services; Diploma of Nursing; Diploma of Leisure and Health</p>
    </section>
    <section>
      <h3>Next Course Commencing</h3>
      <p>Regular intakes are available throughout the year. Please refer to our website at <b>www.brightwardlearning.edu.au</b> for upcoming course dates.</p>
    </section>
  </div>
  <p class="apply"><b>How to Apply Online:</b> <span>Complete an 'online application form' by clicking the below link <b>www.brightwardlearning.edu.au/apply</b></span></p>

  <div class="socials"><i></i><i></i><i></i></div>
  <footer class="footer">
    <span class="footer__item"><span class="footer__icon"></span>admin@bwl.edu.au</span>
    <span class="footer__item"><span class="footer__icon"></span>www.brightwardlearning.edu.au</span>
  </footer>
  <div class="footer__cta">
    APPLY TODAY
    <svg width="12" height="14" viewBox="0 0 12 14"><path d="M3 1h3l1 3-2 1a7 7 0 0 0 3 4l1-2 3 1v3c0 1-1 2-2 2C5 13 0 8 0 3c0-1 1-2 2-2z" fill="#fff"/></svg>
    03 9417 2856
  </div>
</article>

</body>
</html>
```